Business card for Eyelash extension salon in Beverly Hills,California USA

We need new business card for our salon in Beverly Hills. The salon name is 'Lashvera' . We would like to have...Business name: Lashvera Name of person: will provide later Address 4720 N.Alder Crest Ave Beverly Hills , CA 90210 Phone: will provide later (Text only) Web: www.lashverastudio.example Snapgrid icon, Circlebook icon follow us for seasonal campaign and news @lashverastudiolounge Design should look elegant, high-end, clean, simple, cohesive with my brand. Please refer my brand board. Business name color will be metallic bronzy color. Im thinking grey background or white background. Thanks

Target Market(s)

25-35. Gender neutral. People who are in Entertainment business industry.
This is High-end Eyelash extension salon in Beverly Hills

Industry/Entity Type

Beauty Salon

Contact Information for Business Card

Business name: Lashvera
Name of person: will provide later
Address 4720 N.Alder Crest Ave Beverly Hills , CA 90210
Phone: will provide later (Text only)
Web: www.lashverastudio.example
Snapgrid icon, Circlebook icon
follow us for seasonal campaign and news @lashverastudiolounge

Requirements
Must have
• Beautiful, elegant, clean and simple look but very attractive and modern
Should not have
• We don't like too clutter, too busy designs.

```html
<!DOCTYPE html>
<html lang="en">
<head>
<meta charset="utf-8">
<title>Lashvera Business Card</title>
<link rel="stylesheet" href="https://fonts.googleapis.com/css2?family=Merriweather:wght@300;400&family=Playfair+Display:wght@700&family=Montserrat:wght@500&display=swap">
<style>
  :root {
    --backdrop: #e2e2e2;
    --card-front: #ffffff;
    --card-back: #ababab;
    --bronze: #8a6a52;
    --ink: #4a4a4a;
    --muted: #a6a6a6;
    --rule: #9a9a9a;
    --white: #ffffff;
  }
  * { margin: 0; padding: 0; box-sizing: border-box; }
  html, body {
    width: 1200px; height: 960px; overflow: hidden;
    background: var(--backdrop);
  }
  .canvas { position: relative; width: 1200px; height: 960px; }
  .card { position: absolute; width: 600px; height: 343px; }
  .card--front { left: 302px; top: 122px; background: var(--card-front); }
  .card--back { left: 299px; top: 495px; background: var(--card-back); }

  .brand-name {
    position: absolute;
    font-family: "Merriweather", Georgia, serif;
    font-weight: 300;
    white-space: nowrap;
    line-height: 1;
  }
  .brand-locale {
    position: absolute;
    font-family: "Montserrat", Arial, sans-serif;
    font-weight: 500;
    letter-spacing: 1.6px;
    white-space: nowrap;
  }
  .card--front .brand-name { right: 36px; top: 92px; font-size: 50px; color: var(--bronze); }
  .card--front .brand-locale { right: 68px; top: 151px; font-size: 8px; color: var(--bronze); }

  .person-name {
    position: absolute; left: 33px; top: 197px;
    font-family: "Playfair Display", Georgia, serif; font-weight: 700;
    font-size: 25px; letter-spacing: 0.5px; color: var(--bronze);
  }
  .person-role {
    position: absolute; left: 33px; top: 226px;
    font-family: "Merriweather", Georgia, serif; font-size: 13px;
    letter-spacing: 1px; color: var(--muted);
  }
  .person-rule {
    position: absolute; left: 100px; top: 234px; width: 461px; height: 1px;
    background: var(--rule);
  }

  .contact-list {
    position: absolute; left: 33px; top: 255px; list-style: none;
    font-family: "Merriweather", Georgia, serif; font-size: 13.5px; color: var(--ink);
  }
  .contact-item { display: flex; align-items: center; height: 19px; }
  .contact-icon { width: 13px; height: 13px; margin-right: 8px; fill: var(--ink); }

  .address {
    position: absolute; right: 36px; top: 274px; text-align: right;
    font-family: "Merriweather", Georgia, serif; font-size: 13.5px;
    line-height: 18px; color: var(--ink); font-style: normal;
  }

  .card--back .brand-name { left: 0; right: 0; text-align: center; top: 118px; font-size: 64px; color: var(--white); }
  .card--back .brand-locale { left: 297px; top: 217px; font-size: 9px; color: var(--white); }

  .social-list {
    position: absolute; left: 0; right: 0; top: 289px;
    display: flex; justify-content: center; gap: 14px; list-style: none;
    font-family: "Merriweather", Georgia, serif; font-size: 10px; color: var(--white);
  }
</style>
</head>
<body>
<main class="canvas">
  <section class="card card--front">
    <div class="brand-name">Lashvera</div>
    <div class="brand-locale">BEVERLY HILLS</div>

    <h1 class="person-name">MARIKO</h1>
    <p class="person-role">OWNER</p>
    <div class="person-rule"></div>

    <ul class="contact-list">
      <li class="contact-item">
        <svg class="contact-icon" viewBox="0 0 16 16"><path d="M3.5 1 6 1.5 7 5 5.3 6.3a9 9 0 0 0 4.4 4.4L11 9l3.5 1 .5 2.5-1.5 2C7 14.5 1.5 9 1.5 2.5z"/></svg>
        <span>310.555.0142</span>
      </li>
      <li class="contact-item">
        <svg class="contact-icon" viewBox="0 0 16 16"><path d="M1 3.5h14v9H1z"/><path d="M1 3.5 8 9l7-5.5" fill="none" stroke="#fff" stroke-width="1.3"/></svg>
        <span>hello@lashverastudio.example</span>
      </li>
      <li class="contact-item">
        <svg class="contact-icon" viewBox="0 0 16 16"><circle cx="8" cy="8" r="7"/><path d="M4 5.5c1.5 0 2 1 3 1s.5 2 2 2.5-1 3-2 3.5M10 2.5c-.5 1 .5 2 2 2" fill="none" stroke="#fff" stroke-width="1.2"/></svg>
        <span>www.lashverastudio.example</span>
      </li>
    </ul>

    <address class="address">4720 N.Alder Crest Ave<br>Beverly Hills, CA 90210</address>
  </section>

  <section class="card card--back">
    <div class="brand-name">Lashvera</div>
    <div class="brand-locale">BEVERLY HILLS</div>
    <ul class="social-list">
      <li>Circlebook</li>
      <li>Snapgrid</li>
      <li>Reviewly</li>
    </ul>
  </section>
</main>
</body>
</html>
```